Postcard for Direct Mail for a startup company

This will be a postcard for Direct Mail to Churches across America. The size should be around 4" x 6". The front should have our Logo (attached) with the following words:
Audio, Video and Lighting Equipment
Exclusive for churches
DEALER PRICING (This should be what stands out)
tallomix.org and perhaps a URCode.

The front should look trendy and Modern yet clean and sleek. Its important that the reader see "Dealer Pricing" and understand quickly it is for Audio, Video and Lighting equipment.

The back should have room for the Hartwell Courier information where a printer can print the address and such. It should also contain the description paragraph. (attached)

The fonts in the Logo are: SF New Republic and Outfit. This is for informational purposes only. You don't have to use these.

Target Market(s)

Churches / Houses of Worship

Requirements
Must have
• Trendy yet sleek and stylish (modern). Make sure the size works for bulk mailing and postcard.

```html
<!DOCTYPE html>
<html lang="en">
<head>
<meta charset="utf-8">
<title>Tallomix Postcard – Front and Back</title>
<link rel="stylesheet" href="https://fonts.googleapis.com/css2?family=Montserrat:wght@800;900&family=Open+Sans:wght@400;600;700&display=swap">
<style>
  :root {
    --blue: #0b77bd;
    --blue-deep: #0a4fa0;
    --blue-light: #b9d5ec;
    --gold-light: #dd9e44;
    --gold-dark: #a8742e;
    --white: #ffffff;
    --page: #ffffff;
    --grey-soft: #ececec;
    --stamp: #e4e4e4;
  }
  * { box-sizing: border-box; margin: 0; padding: 0; }
  html, body { width: 1200px; height: 2169px; overflow: hidden; background: var(--page); }
  body { position: relative; font-family: "Open Sans", Arial, sans-serif; }

  .postcard {
    position: absolute; left: 80px; width: 1040px; height: 693px;
    background: var(--white); overflow: hidden;
    box-shadow: 0 10px 28px rgba(0,0,0,0.22);
  }
  .postcard--front { top: 346px; }
  .postcard--back { top: 1129px; }

  .heading {
    font-family: "Montserrat", Arial, sans-serif; font-weight: 900;
    color: var(--white); text-transform: uppercase;
  }
  .copy { color: var(--white); font-size: 16.5px; line-height: 21.8px; }

  .stripe { position: absolute; top: 0; height: 100%; display: flex; flex-direction: column; gap: 8px; }
  .stripe span { flex: 1; }
  .stripe span:nth-child(1) { background: linear-gradient(#c7ddef, #8fb8de); }
  .stripe span:nth-child(2) { background: linear-gradient(#8fb8de, #6a9ed2); }
  .stripe span:nth-child(3) { background: linear-gradient(#6a9ed2, #4b88c6); }
  .stripe span:nth-child(4) { background: linear-gradient(#4b88c6, #3776bb); }
  .stripe span:nth-child(5) { background: linear-gradient(#3776bb, #2a67b0); }
  .stripe span:nth-child(6) { background: linear-gradient(#2a67b0, #1c59a6); }
  .stripe span:nth-child(7) { background: linear-gradient(#1c59a6, var(--blue-deep)); }

  .brand-name {
    font-family: "Open Sans", Arial, sans-serif; font-weight: 700;
    color: var(--blue); letter-spacing: 1px;
  }

  .gold { background: linear-gradient(100deg, var(--gold-light), var(--gold-dark)); }

  .category-row { position: absolute; display: flex; }
  .category { text-align: center; color: var(--white); font-weight: 700; }
  .category svg { display: block; margin: 0 auto; }

  /* Front */
  .front-panel { position: absolute; left: 0; top: 0; width: 503px; height: 100%; background: var(--blue); padding: 40px 0 0 57px; }
  .front-title { font-size: 51px; line-height: 49px; letter-spacing: 0.5px; }
  .exclusive-pill {
    display: inline-block; margin-top: 14px; width: 341px; height: 45px; border-radius: 12px;
    color: var(--white); font-weight: 700; font-size: 29px; line-height: 45px; text-align: center; letter-spacing: 0.5px;
  }
  .front-panel .copy { margin-top: 20px; width: 430px; }
  .front-panel .copy + .copy { margin-top: 10px; }
  .dots { margin-top: 16px; display: flex; gap: 4px; }
  .dots i { width: 6px; height: 6px; border-radius: 50%; background: var(--white); }
  .dots i:last-child { background: #7fb2de; }
  .call-to-action { margin-top: 16px; color: var(--white); font-weight: 700; font-size: 30px; line-height: 41px; }
  .front-url { margin-top: 18px; color: var(--white); font-weight: 600; font-size: 23px; letter-spacing: 3.6px; }

  .front-logo { position: absolute; left: 572px; right: 0; top: 52px; text-align: center; font-size: 62px; }
  .pricing-band { position: absolute; left: 572px; right: 0; top: 199px; height: 305px; }
  .pricing-box {
    position: absolute; left: 44px; top: 25px; width: 359px; height: 162px;
    border: 4px solid var(--blue); border-radius: 10px;
    font-size: 74px; line-height: 66px; padding-top: 12px; text-align: center;
  }
  .postcard--front .category-row { left: 24px; top: 205px; }
  .postcard--front .category { width: 126px; font-size: 28px; line-height: 36px; }
  .postcard--front .category + .category { border-left: 1px solid rgba(255,255,255,0.5); }
  .icon-field {
    position: absolute; left: 585px; top: 514px; width: 440px; height: 168px;
    background: linear-gradient(135deg, #f1f1f1, #e2e2e2); border-radius: 4px;
  }

  /* Back */
  .back-info { position: absolute; left: 0; top: 0; width: 486px; height: 290px; background: var(--blue); padding: 34px 0 0 43px; }
  .back-title { font-size: 34px; line-height: 34px; }
  .back-info .copy { margin-top: 22px; width: 420px; }
  .back-notes { position: absolute; left: 0; top: 290px; width: 486px; height: 170px; display: flex; gap: 40px; padding: 18px 0 0 43px; }
  .back-notes .copy { width: 175px; }
  .back-pricing {
    position: absolute; left: 0; top: 460px; width: 486px; height: 57px;
    color: var(--blue); font-family: "Montserrat", Arial, sans-serif; font-weight: 900;
    font-size: 40px; line-height: 57px; text-align: center;
  }
  .back-categories { position: absolute; left: 0; top: 517px; width: 486px; height: 108px; }
  .postcard--back .category-row { left: 40px; top: 14px; }
  .postcard--back .category { width: 135px; font-size: 27px; line-height: 38px; }
  .back-url {
    position: absolute; left: 0; top: 625px; width: 486px; height: 68px;
    color: var(--blue); font-weight: 700; font-size: 27px; line-height: 68px; text-align: center; letter-spacing: 1.6px;
  }
  .back-logo { position: absolute; left: 591px; top: 46px; font-size: 44px; }
  .stamp-box { position: absolute; left: 901px; top: 36px; width: 95px; height: 95px; background: var(--stamp); }
</style>
</head>
<body>

<svg width="0" height="0" style="position:absolute" aria-hidden="true">
  <symbol id="icon-audio" viewBox="0 0 40 32">
    <path d="M3 11h7l9-8v26l-9-8H3z" fill="var(--blue)"/>
    <path d="M24 10q4 6 0 12M28 6q8 10 0 20M32 2q11 14 0 28" stroke="var(--blue)" stroke-width="3" fill="none" stroke-linecap="round"/>
  </symbol>
  <symbol id="icon-video" viewBox="0 0 40 32">
    <circle cx="10" cy="8" r="6" fill="none" stroke="var(--blue)" stroke-width="3.5"/>
    <circle cx="23" cy="8" r="6" fill="none" stroke="var(--blue)" stroke-width="3.5"/>
    <rect x="4" y="15" width="24" height="14" rx="2" fill="var(--blue)"/>
    <path d="M28 22l9-6v12z" fill="var(--blue)"/>
  </symbol>
  <symbol id="icon-lighting" viewBox="0 0 40 32">
    <path d="M10 4l14 10-6 8L4 12z" fill="var(--blue)"/>
    <path d="M21 20l6 8M17 23l3 8M24 16l10 2M26 12l10-4" stroke="var(--blue)" stroke-width="3" stroke-linecap="round"/>
  </symbol>
</svg>

<section class="postcard postcard--front" aria-label="Postcard front">
  <div class="front-panel">
    <h1 class="heading front-title">Audio, Video<br>and Lighting<br>Equipment</h1>
    <div class="exclusive-pill gold">Exclusive for churches</div>
    <p class="copy">Tallomix is a community of like-minded ministry technology enthusiast. We have over 30 years of experience in the industry and currently serve in our local churches. Tallomix is an exclusive church ministry resource for your Audio, Video and Lighting needs.&nbsp; We can help you with products from over 160 manufactures at DEALER PRICING.</p>
    <p class="copy">In order to abide to manufactures minimum advertised pricing policies, you must be registered</p>
    <div class="dots"><i></i><i></i><i></i><i></i></div>
    <p class="call-to-action">Let us help your ministry<br>today at tallomix.org</p>
    <p class="front-url">www.tallomix-demo.com</p>
  </div>
  <div class="stripe" style="left:503px;width:69px"><span></span><span></span><span></span><span></span><span></span><span></span><span></span></div>
  <div class="brand-name front-logo">tallomix</div>
  <div class="pricing-band gold">
    <div class="heading pricing-box">Dealer<br>Pricing</div>
    <div class="category-row">
      <div class="category"><svg width="40" height="32"><use href="#icon-audio"/></svg>Audio</div>
      <div class="category"><svg width="40" height="32"><use href="#icon-video"/></svg>Video</div>
      <div class="category"><svg width="40" height="32"><use href="#icon-lighting"/></svg>Lighting</div>
    </div>
  </div>
  <div class="icon-field" role="img" aria-label="Faint grid of film, camera, projector and stage equipment illustrations"></div>
</section>

<section class="postcard postcard--back" aria-label="Postcard back">
  <div class="back-info">
    <h2 class="heading back-title">Audio, Video and<br>Lighting Equipment</h2>
    <p class="copy">Tallomix is a community of like-minded ministry technology enthusiast. We have over 30 years of experience in the industry and currently serve in our local churches. Tallomix is an exclusive church ministry resource for your Audio, Video and Lighting needs.&nbsp; We can help you with products from over 160 manufactures at DEALER PRICING.</p>
  </div>
  <div class="back-notes gold">
    <p class="copy">Lorem Ipsum is simply dummy text of the printing and typesetting industry. Lorem Ipsum has been the to make a type specimen book.</p>
    <p class="copy">Lorem Ipsum is simply dummy text of the printing and typesetting industry. Lorem Ipsum has been the to make a type specimen book.</p>
  </div>
  <div class="back-pricing">DEALER PRICING</div>
  <div class="back-categories gold">
    <div class="category-row">
      <div class="category"><svg width="40" height="32"><use href="#icon-audio"/></svg>Audio</div>
      <div class="category"><svg width="40" height="32"><use href="#icon-video"/></svg>Video</div>
      <div class="category"><svg width="40" height="32"><use href="#icon-lighting"/></svg>Lighting</div>
    </div>
  </div>
  <div class="back-url">www.tallomix-demo.com</div>
  <div class="stripe" style="left:486px;width:28px"><span></span><span></span><span></span><span></span><span></span><span></span><span></span></div>
  <div class="brand-name back-logo">tallomix</div>
  <div class="stamp-box" aria-label="Postage area"></div>
</section>

</body>
</html>
```